Business Card for Multi-Brand Sportswear Company

We are looking for a business card which represents our company and the multiple brands within it.

The company: Fen Athletics (LTD)
The brands: Fen, TavaPuni, ElmStretch, Grit and Rain

Employees using these cards would be representing Fen Athletics, rather than any of the individual brands. You will see a current design within the uploaded files, to give some inspiration. The actual text of the brands is not necessary, but the logos should be on there is some format.

Our creative minds on this are stretched, so we are looking for someone to make this their own, and show us what a good business card should look like.

We may like to get these printed with spot gloss, so keep that in mind with your designs.

www.fenathletics.co.uk

Industry/Entity Type

Business

Contact Information for Business Card

Leo Pemberton-Hale
Operations Manager
(+44) 1632 960 418
Leo@fenathletics.co.uk
www.fenathletics.co.uk

Font styles to use
Sans Serif
Other font styles liked:
• Eurostile

Colors
ffffff

Requirements
Nice to have
• Dark (black) background

```html
<!DOCTYPE html>
<html lang="en">
<head>
<meta charset="utf-8">
<title>Fen Athletics – Business Card</title>
<link href="https://fonts.googleapis.com/css2?family=Lato:wght@400;700&display=swap" rel="stylesheet">
<style>
  :root {
    --bg-top: #232323;
    --bg-bottom: #060606;
    --card-white: #ffffff;
    --brand-red: #e01f27;
    --brand-red-deep: #b8141b;
    --ink: #1a1a1a;
    --rule: #f2a3a6;
  }
  * { margin: 0; padding: 0; box-sizing: border-box; }
  html, body { width: 1200px; height: 900px; overflow: hidden; }
  body {
    background: linear-gradient(to bottom, var(--bg-top), var(--bg-bottom));
    font-family: "Lato", Arial, sans-serif;
    position: relative;
  }
  .card {
    position: absolute;
    top: 306px;
    width: 438px;
    height: 270px;
    border-radius: 12px;
  }
  .card-front { left: 150px; background: var(--card-white); color: var(--ink); }
  .card-back { left: 609px; background: var(--brand-red); }

  .wordmark {
    position: absolute;
    left: 0; right: 0;
    top: 68px;
    text-align: center;
    font-size: 36px;
    font-weight: 700;
    letter-spacing: 1px;
    color: var(--ink);
  }
  .card-back .wordmark { color: var(--brand-red-deep); top: 62px; }

  .address {
    position: absolute;
    left: 24px; top: 158px;
    font-size: 12px; line-height: 16px;
  }
  .divider {
    position: absolute;
    left: 24px; top: 194px;
    width: 396px; height: 1px;
    background: linear-gradient(to right, var(--rule), var(--brand-red));
  }
  .person {
    position: absolute;
    right: 18px; top: 176px;
    text-align: right;
  }
  .person-name { font-size: 14px; font-weight: 700; color: var(--brand-red); }
  .person-title { font-size: 12px; margin-top: 6px; }

  .contacts {
    position: absolute;
    left: 24px; top: 202px;
    list-style: none;
    font-size: 12px; line-height: 16px;
  }
  .contacts li { display: flex; align-items: center; gap: 6px; }
  .contacts svg { width: 8px; height: 8px; fill: var(--brand-red); }

  .brand-row {
    position: absolute;
    left: 0; right: 0; top: 180px;
    display: flex; justify-content: center; align-items: center; gap: 22px;
  }
  .brand-name {
    color: var(--card-white);
    font-size: 12px; font-weight: 700;
    letter-spacing: 0.5px;
  }
</style>
</head>
<body>
  <section class="card card-front">
    <div class="wordmark">Fen Athletics</div>
    <p class="address">Marsh Lane, Eastby,<br>Thornholt, YO9 4QT</p>
    <div class="person">
      <p class="person-name">Leo Pemberton-Hale</p>
      <p class="person-title">Managing Director</p>
    </div>
    <div class="divider"></div>
    <ul class="contacts">
      <li><svg viewBox="0 0 8 8"><path d="M1 1h2l1 2-1 1a4 4 0 0 0 1 1l1-1 2 1v2h-1A6 6 0 0 1 1 2z"/></svg>+44(0)1632 960418</li>
      <li><svg viewBox="0 0 8 8"><rect x="0" y="1.5" width="8" height="5" rx="0.5"/></svg>leo@fenathletics.co.uk</li>
      <li><svg viewBox="0 0 8 8"><circle cx="4" cy="4" r="4"/></svg>www.fenathletics.co.uk</li>
    </ul>
  </section>

  <section class="card card-back">
    <div class="wordmark">Fen Athletics</div>
    <div class="brand-row">
      <span class="brand-name">Grit and Rain</span>
      <span class="brand-name">ElmStretch</span>
      <span class="brand-name">TavaPuni</span>
      <span class="brand-name">Fen</span>
    </div>
  </section>
</body>
</html>
```